Window Treatment business needs website redesigned.

We need a revamp and refresh of our current site www.velmarix.ca
Looking to attract very high end customer. It should be a very simple design with very little text. This site will be visited by prospective homeowners, designers, builders and architects. They should feel that they are dealing with a high-end product selection, where experience, customer service and unique product offering is the focus. The content will be to highlight our services and highlight the manufacturers we sell, using a few rich photos to highlight the products. We should NOT look like we are a very large company. It should NOT have discounts/savings buttons and many menus to choose from. We offer over 15 years experience to narrow the many market options, to provide the right technical solution.
We specialize in products that are not readily available on the market and specifically motorized systems for indoors and outdoors.
Our main suppliers are Kravenholt.com, Dimbrell.com
We carry our own locally manufactured product line of roller shades.
Main product pictures should be of roller shades, outdoor bug screens, awnings and outdoor pergolas.

Reason: I understand that Christmas is coming up real short and many people are extremely busy. If you have a CREATIVE gifting you still want to submit, I look forward to your idea!

Reason: Due to holiday season, we have not had sufficient time to review to make a final decision. Thank you for your patience!

Target Market(s)

High end home owners, designers, builders, architects

Industry/Entity Type

Contractor

Coding

Coded - Design and coding required

Number of Pages Required

3 page

Font styles to use
Sans Serif

Requirements
Must have
• Landing page with full size image like homepage of zolvane.it
• Products page that highlights products with simple product shot image, description and link to manufacturer.
• On main page a scrolling of customer reviews.
• I want a very simple, eye-catching, emotional image for homepage. It does not need to include any product image.
• An image that shows technology combining/meshing with hand craftsmanship.
• Focus is on design.
• http://www.zolvane.it/en/gallery is a great layout and design.
Nice to have
• Logo shape for icons and watermark should be used.
• Look like and have simple motion effects like quorix.com or telvarin.com
Should not have
• Generic/standard looking feel like bluppet.com or mecklorwindow.ca
• No use of green as background only subtle text.
• Lots of text and pages.

```html
<!DOCTYPE html>
<html lang="en">
<head>
<meta charset="utf-8">
<title>Velmarix – Insect Screens</title>
<link href="https://fonts.googleapis.com/css2?family=Montserrat:wght@400;500;600;700&display=swap" rel="stylesheet">
<style>
  :root {
    --green: #6cc04a;
    --ink: #444a4f;
    --charcoal: rgba(38, 42, 45, 0.86);
    --grey-text: #6a6e72;
    --white: #ffffff;
    --section-bg: #f6f7f7;
    --hero-sky: #8fa6c4;
    --hero-wall: #b7ab99;
    --hero-rail: #4b4039;
  }
  * { box-sizing: border-box; margin: 0; padding: 0; }
  html, body { width: 1200px; height: 841px; overflow: hidden; }
  body {
    position: relative;
    font-family: "Montserrat", Arial, sans-serif;
    background: var(--white);
    color: var(--ink);
  }

  /* Hero */
  .hero {
    position: absolute; left: 0; top: 0;
    width: 1200px; height: 578px;
    background:
      linear-gradient(90deg, rgba(60,50,42,0.35) 0%, rgba(0,0,0,0) 45%, rgba(0,0,0,0.08) 100%),
      linear-gradient(160deg, var(--hero-rail) 0%, var(--hero-wall) 30%, #c8bfb1 50%, #7d6f62 70%, var(--hero-sky) 100%);
  }
  .hero-frame {
    position: absolute; left: 32px; top: 29px;
    width: 1135px; height: 521px;
    border: 2px solid rgba(255,255,255,0.85);
  }
  .hero-title {
    position: absolute; left: 674px; top: 222px;
    font-size: 47px; font-weight: 700; letter-spacing: 1px; line-height: 56px;
    color: var(--white);
  }
  .hero-tagline {
    position: absolute; left: 678px; top: 287px; width: 440px;
    font-size: 21.5px; font-weight: 400; line-height: 28px; letter-spacing: 0.5px;
    color: var(--white);
  }
  .slider-dots {
    position: absolute; left: 563px; top: 500px;
    display: flex; gap: 14px;
  }
  .slider-dots span {
    width: 8px; height: 8px; border-radius: 50%;
    border: 1.5px solid var(--white);
  }

  /* Customer reviews ticker */
  .reviews {
    position: absolute; left: 200px; top: 418px;
    width: 330px; height: 62px;
    overflow: hidden;
    color: var(--white);
  }
  .reviews-label {
    font-size: 10px; font-weight: 600; letter-spacing: 2px; text-transform: uppercase;
    color: var(--green); margin-bottom: 6px;
  }
  .reviews-window { height: 40px; overflow: hidden; }
  .reviews-track { animation: reviews-scroll 12s infinite; }
  .review { height: 40px; font-size: 12px; line-height: 17px; }
  .review cite { font-style: normal; font-size: 10px; opacity: 0.8; }
  @keyframes reviews-scroll {
    0%, 28% { transform: translateY(0); }
    33%, 61% { transform: translateY(-40px); }
    66%, 95% { transform: translateY(-80px); }
    100% { transform: translateY(0); }
  }

  /* Header & nav */
  .menu-toggle {
    position: absolute; left: 0; top: 28px;
    width: 58px; height: 59px;
    background: var(--charcoal);
    display: flex; align-items: center; justify-content: center;
  }
  .brand {
    position: absolute; left: 58px; top: 28px;
    width: 194px; height: 59px;
    background: var(--white);
    display: flex; align-items: center; gap: 9px; padding-left: 14px;
  }
  .brand-mark { width: 16px; height: 16px; border-radius: 50%; background: var(--ink); }
  .brand-name { font-size: 22px; font-weight: 500; color: var(--ink); letter-spacing: 0.5px; }
  .main-nav {
    position: absolute; left: 0; top: 87px;
    width: 165px; height: 262px;
    background: var(--charcoal);
    padding-top: 20px;
  }
  .main-nav ul { list-style: none; }
  .main-nav li {
    display: flex; align-items: center;
    height: 27px; padding-left: 23px;
    font-size: 13.5px; color: var(--white);
  }
  .main-nav li svg { margin-right: 16px; }

  /* Partners */
  .partners {
    position: absolute; left: 0; top: 578px;
    width: 1200px; height: 214px;
    background: linear-gradient(180deg, #f3f4f4 0%, var(--section-bg) 100%);
  }
  .partners-title {
    position: absolute; left: 0; top: 51px; width: 1200px;
    text-align: center; font-size: 25px; font-weight: 700; color: var(--ink);
  }
  .partners-title em { font-style: normal; color: var(--green); }
  .partners-rule {
    position: absolute; left: 154px; width: 892px;
    border-top: 1px dashed var(--green);
  }
  .partners-rule.top { top: 108px; }
  .partners-rule.bottom { top: 203px; }
  .partner-list {
    position: absolute; left: 0; top: 140px; width: 1200px;
    display: flex; justify-content: center; gap: 110px;
  }
  .partner-name {
    font-size: 24px; font-weight: 500; color: var(--grey-text); letter-spacing: 0.5px;
    display: flex; align-items: center; gap: 8px;
  }
  .partner-name i { width: 12px; height: 12px; background: var(--grey-text); display: block; }

  /* Footer */
  .site-footer {
    position: absolute; left: 0; top: 798px;
    width: 1200px; height: 43px;
    background: var(--white);
  }
  .copyright {
    position: absolute; left: 0; top: 14px; width: 1200px;
    text-align: center; font-size: 10.5px; color: var(--grey-text);
  }
  .page-code {
    position: absolute; left: 1119px; top: 14px;
    font-size: 10.5px; color: #9a9ea2;
  }
</style>
</head>
<body>

  <section class="hero" role="img" aria-label="Photograph of an apartment building corner with balconies fitted with insect screens against a blue sky">
    <div class="hero-frame"></div>
    <h1 class="hero-title">Insect Screens</h1>
    <p class="hero-tagline">Modern wind and rain Systems with aluminium of fabric root systems</p>
    <div class="slider-dots"><span></span><span></span><span></span><span></span></div>
  </section>

  <aside class="reviews" aria-label="Customer reviews">
    <p class="reviews-label">Client Reviews</p>
    <div class="reviews-window">
      <div class="reviews-track">
        <p class="review">“Flawless motorized shades, installed with real care.”<br><cite>— Homeowner</cite></p>
        <p class="review">“The right technical solution for every opening.”<br><cite>— Architect</cite></p>
        <p class="review">“Unique products and truly personal service.”<br><cite>— Interior Designer</cite></p>
      </div>
    </div>
  </aside>

  <div class="menu-toggle">
    <svg width="24" height="20" viewBox="0 0 24 20" aria-hidden="true">
      <rect x="0" y="1" width="24" height="2" fill="#fff"/>
      <rect x="0" y="9" width="24" height="2" fill="#fff"/>
      <rect x="0" y="17" width="24" height="2" fill="#fff"/>
    </svg>
  </div>
  <div class="brand">
    <span class="brand-mark"></span>
    <span class="brand-name">Velmarix</span>
  </div>

  <nav class="main-nav">
    <ul>
      <li><svg width="6" height="9" viewBox="0 0 6 9"><path d="M1 1l3.5 3.5L1 8" fill="none" stroke="#6cc04a" stroke-width="1.3"/></svg>Home</li>
      <li><svg width="6" height="9" viewBox="0 0 6 9"><path d="M1 1l3.5 3.5L1 8" fill="none" stroke="#6cc04a" stroke-width="1.3"/></svg>Shades</li>
      <li><svg width="6" height="9" viewBox="0 0 6 9"><path d="M1 1l3.5 3.5L1 8" fill="none" stroke="#6cc04a" stroke-width="1.3"/></svg>Insect Screens</li>
      <li><svg width="6" height="9" viewBox="0 0 6 9"><path d="M1 1l3.5 3.5L1 8" fill="none" stroke="#6cc04a" stroke-width="1.3"/></svg>Awnings</li>
      <li><svg width="6" height="9" viewBox="0 0 6 9"><path d="M1 1l3.5 3.5L1 8" fill="none" stroke="#6cc04a" stroke-width="1.3"/></svg>Pergolas</li>
      <li><svg width="6" height="9" viewBox="0 0 6 9"><path d="M1 1l3.5 3.5L1 8" fill="none" stroke="#6cc04a" stroke-width="1.3"/></svg>Latest projects</li>
      <li><svg width="6" height="9" viewBox="0 0 6 9"><path d="M1 1l3.5 3.5L1 8" fill="none" stroke="#6cc04a" stroke-width="1.3"/></svg>Contact us</li>
      <li><svg width="6" height="9" viewBox="0 0 6 9"><path d="M1 1l3.5 3.5L1 8" fill="none" stroke="#6cc04a" stroke-width="1.3"/></svg>Mediaroom</li>
    </ul>
  </nav>

  <section class="partners">
    <h2 class="partners-title">Industry <em>Partners</em></h2>
    <div class="partners-rule top"></div>
    <div class="partner-list">
      <span class="partner-name">Lumacrest</span>
      <span class="partner-name"><i></i>Kravenholt</span>
    </div>
    <div class="partners-rule bottom"></div>
  </section>

  <footer class="site-footer">
    <p class="copyright">Copyrights © 2017, www.companyname.com . All Rights Reserved.</p>
    <span class="page-code">M1</span>
  </footer>

</body>
</html>
```